Business Card For Halvenmoor Financial Consulting

Hi, I would like a business card designed. Bold, modern.
Please use the same design as the logo. I have also attached the website design to see the overall theme.
Wordmark Font
Color: Hex: #01AEF7

```html
<!DOCTYPE html>
<html lang="en">
<head>
<meta charset="utf-8">
<title>Halvenmoor Financial Consulting – Business Card</title>
<link rel="stylesheet" href="https://fonts.googleapis.com/css2?family=Arimo:wght@400;700&display=swap">
<style>
  :root {
    --brand-blue: #01aef7;
    --brand-blue-deep: #0a9fe6;
    --ink: #17222c;
    --text-grey: #5a5f66;
    --divider: #8a8f95;
    --paper: #f7f7f5;
    --backdrop: #1c1d1f;
  }
  * { box-sizing: border-box; margin: 0; padding: 0; }
  html, body { width: 1200px; height: 963px; overflow: hidden; }
  body {
    background: var(--backdrop);
    font-family: "Arimo", Arial, sans-serif;
    display: flex;
    flex-direction: column;
    align-items: center;
    justify-content: center;
    gap: 56px;
  }
  .card {
    width: 600px;
    height: 343px;
    border-radius: 22px;
    position: relative;
    overflow: hidden;
  }
  /* Front */
  .card--front {
    background: var(--paper);
    display: flex;
    align-items: center;
    padding: 0 44px 0 48px;
  }
  .brand {
    display: flex;
    align-items: center;
    gap: 12px;
    width: 270px;
  }
  .brand__square {
    width: 30px; height: 30px;
    border: 4px solid var(--brand-blue);
    flex: none;
  }
  .brand__name {
    color: var(--ink);
    font-weight: 700;
    font-size: 21px;
    line-height: 1.15;
    letter-spacing: 0.5px;
    text-transform: uppercase;
  }
  .divider {
    width: 1.5px;
    height: 178px;
    background: var(--divider);
    margin: 0 28px 0 6px;
  }
  .contact { color: var(--text-grey); font-size: 15px; line-height: 1.35; }
  .contact__name {
    color: var(--brand-blue);
    font-weight: 700;
    font-size: 20px;
    text-transform: uppercase;
    letter-spacing: 0.3px;
  }
  .contact__role { margin-bottom: 12px; }
  .contact__address { margin-bottom: 12px; }
  .contact__line { display: flex; align-items: center; gap: 9px; }
  .contact__icon { width: 14px; height: 14px; flex: none; fill: var(--brand-blue); }
  /* Back */
  .card--back {
    background: linear-gradient(135deg, var(--brand-blue) 0%, var(--brand-blue-deep) 100%);
    display: flex;
    align-items: center;
    justify-content: center;
  }
  .back__mark {
    display: flex; align-items: center; gap: 16px;
  }
  .back__square { width: 40px; height: 40px; border: 5px solid #fff; }
  .back__name {
    color: #fff;
    font-weight: 700;
    font-size: 34px;
    letter-spacing: 1px;
    text-transform: uppercase;
    line-height: 1.1;
  }
</style>
</head>
<body>
  <section class="card card--front" aria-label="Business card front">
    <div class="brand">
      <span class="brand__square"></span>
      <span class="brand__name">Halvenmoor<br>Consulting</span>
    </div>
    <span class="divider"></span>
    <div class="contact">
      <p class="contact__name">Marcus Ellery</p>
      <p class="contact__role">Manager</p>
      <p class="contact__address">Your Address, City<br>State, Zip 0000</p>
      <p class="contact__line">
        <svg class="contact__icon" viewBox="0 0 24 24"><path d="M6.6 10.8a15.1 15.1 0 0 0 6.6 6.6l2.2-2.2a1 1 0 0 1 1-.25 11.4 11.4 0 0 0 3.6.57 1 1 0 0 1 1 1V20a1 1 0 0 1-1 1A17 17 0 0 1 3 4a1 1 0 0 1 1-1h3.5a1 1 0 0 1 1 1c0 1.25.2 2.45.57 3.57a1 1 0 0 1-.25 1z"/></svg>
        123-456-2100
      </p>
      <p class="contact__line">
        <svg class="contact__icon" viewBox="0 0 24 24"><path d="M2 5h20v14H2z M2 5l10 8 10-8" fill="none" stroke="#01aef7" stroke-width="2.4"/></svg>
        youremail@mailbox.com
      </p>
      <p class="contact__line">
        <svg class="contact__icon" viewBox="0 0 24 24"><circle cx="12" cy="12" r="9.5" fill="none" stroke="#01aef7" stroke-width="2.4"/><path d="M2.5 12h19M12 2.5c3 3 3 16 0 19M12 2.5c-3 3-3 16 0 19" fill="none" stroke="#01aef7" stroke-width="2"/></svg>
        www.yourwebsite.com
      </p>
    </div>
  </section>

  <section class="card card--back" aria-label="Business card back">
    <div class="back__mark">
      <span class="back__square"></span>
      <span class="back__name">Halvenmoor<br>Consulting</span>
    </div>
  </section>
</body>
</html>
```